Business Card For Halvenmoor Financial Consulting

Hi, I would like a business card designed. Bold, modern.
Please use the same design as the logo. I have also attached the website design to see the overall theme.
Wordmark Font
Color: Hex: #01AEF7

```html
<!DOCTYPE html>
<html lang="en">
<head>
<meta charset="utf-8">
<title>Halvenmoor Financial Consulting – Business Card</title>
<link href="https://fonts.googleapis.com/css2?family=Lato:wght@400;700&family=Montserrat:wght@600;700&display=swap" rel="stylesheet">
<style>
  :root {
    --stage: #cfcfd0;
    --card: #15202b;
    --card-deep: #101a23;
    --accent: #01aef7;
    --ink-light: #e9eef2;
    --ink-muted: #c9d3da;
  }
  * { box-sizing: border-box; margin: 0; padding: 0; }
  html, body { width: 1200px; height: 997px; overflow: hidden; }
  body {
    background: var(--stage);
    position: relative;
    font-family: "Lato", sans-serif;
  }
  .card {
    position: absolute;
    width: 560px;
    height: 320px;
    background: var(--card);
    border-radius: 3px;
    box-shadow: 0 18px 40px rgba(0,0,0,.28);
    overflow: hidden;
  }
  /* Back side */
  .card--back { left: 50px; top: 150px; }
  .back-pattern {
    position: absolute; inset: 0;
    background: linear-gradient(120deg, #1d3650 0%, #15202b 45%, var(--card-deep) 100%);
  }
  .brand-name {
    position: absolute;
    left: 0; right: 0; top: 50%;
    transform: translateY(-50%);
    text-align: center;
    font-family: "Montserrat", sans-serif;
    font-weight: 700;
    font-size: 30px;
    color: var(--ink-light);
    line-height: 1;
  }
  /* Front side */
  .card--front { left: 600px; top: 520px; }
  .holder {
    position: absolute;
    left: 40px; bottom: 70px;
  }
  .holder-name {
    font-family: "Montserrat", sans-serif;
    font-weight: 700;
    font-size: 28px;
    color: var(--accent);
    letter-spacing: .5px;
  }
  .holder-role {
    font-size: 17px;
    color: var(--ink-light);
    margin-top: 2px;
  }
  .divider {
    position: absolute;
    left: 292px; top: 60px;
    width: 2px; height: 200px;
    background: linear-gradient(to bottom, transparent, var(--accent), transparent);
  }
  .contact {
    position: absolute;
    left: 312px; top: 54px;
    font-size: 14px;
    line-height: 21px;
    color: var(--ink-muted);
    list-style: none;
  }
  .contact-company { color: var(--accent); font-size: 15px; }
  .contact-row { display: flex; align-items: center; gap: 8px; }
  .contact-row svg { width: 12px; height: 12px; flex: none; fill: var(--accent); }
</style>
</head>
<body>

<section class="card card--back">
  <div class="back-pattern" role="img" aria-label="Repeated brand pattern in navy and sky blue tones"></div>
  <p class="brand-name">Halvenmoor Consulting</p>
</section>

<section class="card card--front">
  <div class="holder">
    <p class="holder-name">DANIEL CRANE</p>
    <p class="holder-role">Founder &amp; CEO</p>
  </div>
  <span class="divider"></span>
  <ul class="contact">
    <li class="contact-company">Halvenmoor Financial Consulting</li>
    <li>Your Address, City</li>
    <li>State, Zip Code 1235</li>
    <li class="contact-row">
      <svg viewBox="0 0 12 12"><path d="M2.5 1l2 2-1 1.5c.6 1.5 1.5 2.4 3 3L8 6.5l2 2L9 10.5C5 10.5 1.5 7 1.5 3z"/></svg>
      (555) 214-3080
    </li>
    <li class="contact-row">
      <svg viewBox="0 0 12 12"><path d="M3.5 1h5v10h-5z M4.5 2v7h3V2z"/></svg>
      (555) 214-3081
    </li>
    <li class="contact-row">
      <svg viewBox="0 0 12 12"><path d="M3 1h6v3H3z M1.5 5h9v5h-1.5V8h-6v2H1.5z M3.5 9h5v2h-5z"/></svg>
      (555) 214-3082
    </li>
    <li class="contact-row">
      <svg viewBox="0 0 12 12"><path d="M1 3h10v6H1z M1.5 3.5L6 7l4.5-3.5" stroke="#15202b" stroke-width=".8"/></svg>
      info@halvenmoorconsulting.com
    </li>
    <li class="contact-row">
      <svg viewBox="0 0 12 12"><circle cx="6" cy="6" r="5"/><path d="M1 6h10M6 1c-2 2.5-2 7.5 0 10M6 1c2 2.5 2 7.5 0 10" stroke="#15202b" stroke-width=".8" fill="none"/></svg>
      halvenmoorconsulting.com
    </li>
  </ul>
</section>

</body>
</html>
```